Verodex business card

Business card for sustainable investment company called "Verodex". Verodex is an exchange platform selling carbon credits between buyers and sellers. Carbon Credits are an environmental commodity for reducing global carbon emissions.

the card should obviously have our logo and the theme should be sustainability/environment mixed with a trading platform.

Contact Information for Business Card

Logo, Name, Title, Phone, Email

Colors
0054AA
0677BA
7BADD7
CADEEF
E8F1F8
0094D4
00A9DD
6FCCEA
C7EBF8
E9F6FB
00AB8E
00BBA5
67D7C9
C6EFE9
E9F9F6
59FF00
82FF00
B8FF75
E3FFCB
F4FFEA

```html
<!DOCTYPE html>
<html lang="en">
<head>
<meta charset="utf-8">
<title>Verodex business card</title>
<link href="https://fonts.googleapis.com/css2?family=Raleway:wght@400;500;700&display=swap" rel="stylesheet">
<style>
  :root{
    --stage:#1d1d20;
    --paper:#ffffff;
    --ink:#1b2a44;
    --ink-soft:#3d4450;
    --accent:#1fa3e6;
    --cyan:#35e6ec;
    --sky:#2aa8e8;
    --blue:#1e6ee8;
  }
  *{box-sizing:border-box;margin:0;padding:0}
  html,body{width:1200px;height:718px;overflow:hidden;background:var(--stage)}
  body{font-family:"Raleway",sans-serif;position:relative}
  .card{
    position:absolute;top:209px;width:520px;height:300px;
    background:var(--paper);border-radius:16px;overflow:hidden;
  }
  .card--front{left:45px}
  .card--back{left:635px}

  .brand-art{position:absolute;top:0;bottom:0}
  .card--front .brand-art{right:0;width:190px;background:linear-gradient(135deg,var(--cyan),var(--sky))}
  .card--back .brand-art{left:0;width:230px;background:linear-gradient(135deg,var(--sky),var(--blue))}

  .logo{position:absolute;left:34px;top:132px;display:flex;align-items:center;gap:12px}
  .logo__mark{width:34px;height:34px;border-radius:50%;background:var(--sky)}
  .logo__name{font-weight:700;font-size:32px;color:var(--ink);letter-spacing:.5px}

  .contact{position:absolute;right:34px;top:130px;text-align:right}
  .contact__name{font-weight:700;font-size:26px;color:var(--accent);letter-spacing:.5px}
  .contact__title{font-size:15px;color:var(--ink-soft);margin-top:2px}
  .contact__list{list-style:none;margin-top:16px}
  .contact__item{display:flex;justify-content:flex-end;align-items:center;gap:10px;font-size:13.5px;color:var(--ink-soft);line-height:22px}
  .contact__icon{width:13px;height:13px;flex:none}
</style>
</head>
<body>
  <section class="card card--front">
    <div class="logo">
      <span class="logo__mark"></span>
      <span class="logo__name">VERODEX</span>
    </div>
    <div class="brand-art" role="img" aria-label="Large brand mark decoration in cyan gradient"></div>
  </section>

  <section class="card card--back">
    <div class="brand-art" role="img" aria-label="Large brand mark decoration in blue gradient"></div>
    <div class="contact">
      <h1 class="contact__name">MARCUS HALE</h1>
      <p class="contact__title">Founder &amp; CEO</p>
      <ul class="contact__list">
        <li class="contact__item">(555) 214-7730
          <svg class="contact__icon" viewBox="0 0 24 24"><path fill="#1fa3e6" d="M6.6 10.8a15 15 0 0 0 6.6 6.6l2.2-2.2a1 1 0 0 1 1-.25 11.4 11.4 0 0 0 3.6.57 1 1 0 0 1 1 1V20a1 1 0 0 1-1 1A17 17 0 0 1 3 4a1 1 0 0 1 1-1h3.5a1 1 0 0 1 1 1c0 1.25.2 2.45.57 3.57a1 1 0 0 1-.25 1z"/></svg>
        </li>
        <li class="contact__item">office@verodex.com
          <svg class="contact__icon" viewBox="0 0 24 24"><rect x="2" y="5" width="20" height="14" rx="1" fill="#1fa3e6"/><path d="M2 6l10 7 10-7" fill="none" stroke="#fff" stroke-width="1.6"/></svg>
        </li>
        <li class="contact__item">verodex.com
          <svg class="contact__icon" viewBox="0 0 24 24"><circle cx="12" cy="12" r="10" fill="none" stroke="#1fa3e6" stroke-width="2"/><ellipse cx="12" cy="12" rx="4" ry="10" fill="none" stroke="#1fa3e6" stroke-width="1.6"/><path d="M2 12h20" stroke="#1fa3e6" stroke-width="1.6"/></svg>
        </li>
      </ul>
    </div>
  </section>
</body>
</html>
```